Business Card Design for my Real Estate Investing Company

This is for a Real Estate Investing Company that will be serving the Las Vegas Valley. Id like the following slogan included: "Investing in Our Community" I have attached my logo. You will see the color tones I'm interested in..in my logo. I would like the card to be double-sided with a modern, professional look.
Target Market(s)
Homeowners, banks, real estate industry
Industry/Entity Type
Real Estate
Contact Information for Business Card
name: Dale Harwick
position: Managing Member
address: 4821 Corliss Pkwy ste 207-300
N. Las Vegas, NV 89084
phone: (702) 555-0143
fax: (702) 555-0187
email: SummitRidgeEstate@hollowmail.test
web: SummitRidgeEstates.test
*At the bottom of the card I would like....
We buy houses for cash....no repairs, no commissions, no fees!
Logo Text
SUMMIT RIDGE ESTATES "Investing in Our Community"
Font styles to use
Other font styles liked:
- Lora
Requirements
Must have
- On the back of the card, i'd like to have my logo large and the following statements:
- Are you considering selling your home? Want a simple, hassle-free transaction? We can help! We buy houses for cash and can close quickly! No need to do any repairs, no realtor commissions, no closing costs.....and no headaches. Let us help you with your real estate needs...!
Nice to have
- multiple colors 2 two tone on front and back

```html
<!DOCTYPE html>
<html lang="en">
<head>
<meta charset="utf-8">
<title>Summit Ridge Estates – Business Card</title>
<link href="https://fonts.googleapis.com/css2?family=Source+Sans+3:ital,wght@0,400;0,600;1,400&display=swap" rel="stylesheet">
<style>
  :root {
    --backdrop: #e4e5e8;
    --card-black: #141416;
    --card-black-soft: #232326;
    --brand-blue: #1b5fb0;
    --brand-blue-light: #2c78d1;
    --swoosh-white: #e9eaec;
    --text-white: #f4f4f4;
    --text-grey: #d9d9d9;
  }
  * { box-sizing: border-box; margin: 0; padding: 0; }
  html, body {
    width: 1200px; height: 900px; overflow: hidden;
    background: var(--backdrop);
    font-family: "Source Sans 3", "Myriad Pro", Arial, sans-serif;
  }
  .stage { position: relative; width: 1200px; height: 900px; }

  .card {
    position: absolute; width: 700px; height: 400px;
    background: radial-gradient(ellipse at 40% 30%, var(--card-black-soft), var(--card-black) 75%);
    border-radius: 4px; overflow: hidden;
    box-shadow: 0 10px 28px rgba(0,0,0,.25);
    color: var(--text-white);
  }

  /* Back side */
  .card-back { left: 110px; top: 40px; text-align: center; }
  .brand-block { padding-top: 58px; }
  .brand-name {
    display: inline-flex; align-items: center; gap: 14px;
    font-weight: 600; font-size: 44px; letter-spacing: 3px;
    color: var(--brand-blue-light);
  }
  .brand-square { width: 30px; height: 30px; background: var(--brand-blue-light); }
  .brand-slogan {
    margin-top: 8px; font-size: 20px; letter-spacing: 5px;
    color: var(--text-white);
  }
  .pitch {
    margin-top: 40px; font-size: 21px; line-height: 1.28;
    color: var(--text-white);
  }

  /* Front side */
  .card-front { left: 390px; top: 470px; }
  .wave { position: absolute; left: 0; top: 0; width: 700px; height: 400px; }
  .contact { position: absolute; left: 50px; top: 34px; z-index: 1; }
  .contact-name { font-size: 24px; font-weight: 600; line-height: 1.2; color: var(--brand-blue-light); }
  .contact-role { font-size: 17px; color: var(--text-grey); margin-top: 2px; }
  .contact-address { font-size: 17px; line-height: 1.25; margin-top: 16px; color: var(--text-grey); }
  .contact-lines { list-style: none; margin-top: 14px; }
  .contact-lines li {
    display: flex; align-items: center; gap: 10px;
    font-size: 17px; line-height: 1.25; color: var(--text-white);
  }
  .contact-lines svg { width: 14px; height: 14px; fill: var(--brand-blue-light); flex: none; }
  .front-brand {
    position: absolute; right: 42px; top: 66px;
    display: flex; align-items: center; gap: 10px;
    font-weight: 600; font-size: 20px; letter-spacing: 2px;
    color: var(--brand-blue-light);
  }
  .front-brand .brand-square { width: 18px; height: 18px; }
  .tagline {
    position: absolute; right: 28px; top: 300px;
    text-align: right; font-size: 16px; line-height: 1.25;
    color: var(--text-white);
  }
</style>
</head>
<body>
<main class="stage">

  <section class="card card-back" aria-label="Card back">
    <div class="brand-block">
      <div class="brand-name"><span class="brand-square"></span>SUMMIT RIDGE ESTATES</div>
      <p class="brand-slogan">“Investing in Our Community”</p>
    </div>
    <p class="pitch">
      Are you considering selling your home?<br>
      Want a simple, hassle-free transaction?<br>
      We can help! We buy houses for cash and<br>
      can close quickly! No need to do any repairs,<br>
      no realtor commissions, no closing costs.....<br>
      and no headaches. Let us help you with your real estate needs...!
    </p>
  </section>

  <section class="card card-front" aria-label="Card front">
    <svg class="wave" viewBox="0 0 700 400" aria-hidden="true">
      <path d="M0 312 C160 332 320 312 440 252 C540 202 610 185 700 182 L700 400 L0 400 Z" fill="var(--swoosh-white)"/>
      <path d="M0 336 C170 348 330 325 455 265 C550 218 620 198 700 192 L700 400 L0 400 Z" fill="var(--card-black)"/>
      <path d="M0 356 C190 366 350 340 470 276 C560 228 630 200 700 188 L700 400 L0 400 Z" fill="var(--brand-blue)"/>
    </svg>

    <div class="contact">
      <h1 class="contact-name">Dale Harwick</h1>
      <p class="contact-role">Managing Member</p>
      <p class="contact-address">4821 Corliss Pkwy ste 207-300<br>N. Las Vegas, NV 89084</p>
      <ul class="contact-lines">
        <li><svg viewBox="0 0 16 16"><path d="M3 1h3l1.5 4-2 1.3a9 9 0 0 0 4.2 4.2L11 8.5l4 1.5v3c0 1-1 2-2 2C6.5 15 1 9.5 1 3c0-1 1-2 2-2z"/></svg>(702) 555-0143</li>
        <li><svg viewBox="0 0 16 16"><path d="M4 1h7l1 1v4H4zM1 7h14v6h-3v2H4v-2H1zM5 11v3h6v-3z"/></svg>(702) 555-0187</li>
        <li><svg viewBox="0 0 16 16"><path d="M1 3h14v10H1zM2 4v.5l6 4 6-4V4z"/></svg>SummitRidgeEstate@hollowmail.test</li>
        <li><svg viewBox="0 0 16 16"><circle cx="8" cy="8" r="7"/></svg>SummitRidgeEstates.test</li>
      </ul>
    </div>

    <div class="front-brand"><span class="brand-square"></span>SUMMIT RIDGE ESTATES</div>

    <p class="tagline">We buy houses for cash....no repairs,<br>no commissions, no fees!</p>
  </section>

</main>
</body>
</html>
```